AUTOMOTIVE/ CAR REPAIRS / CRASH REPAIRS / PAINT SPRAYING AND PANEL BEATING

AUTOMOTIVE REPAIR. CAR / MOTORCYCLES GOT LOGO DESIGN / DID THINK ABOUT FACEBOOK DONT NOALREADY HAVE WEB ADRESS www.brenvashine.co.uk and mail sales@brenvashine,co.uk NEED SOMETHINK I CAN MANAGE TO UPLOAD PICTURES IN TO A GALLERY OR SOMETHINGLIKE THAT I ALSO SELL CAR AND MOTORCYCLES MAYBE A SELLS PAGE WITH A TILLWAVE LINK

Target Market(s)

TRADE / GENERAL PUBLIC

Industry/Entity Type

Automotive

Coding

Coded - Design and coding required

Number of Pages Required

4 page

Font styles to use
Serif
Sans Serif

Colors

Designer to choose colors to be used in the design.

Requirements
Must have
• GALLERY/ SHOP TO SALE CARS AND MOTORCYCLE / LOGOS OF MATERIALS I USE DORFLINT / KEBO / VASTINCO / Q WRAP / GLENBRUSH
• CONTACT US
Nice to have
• TILLWAVE / EASY TO MANAGE / VIDEO CLIP OF DORFLINT HUE PLANNER Z7
• SWIFT BLEND PAINT TONVIEW WETLINE AND TULVOKE

```html
<!DOCTYPE html>
<html lang="en">
<head>
<meta charset="utf-8">
<title>Brenvashine Bodyshop</title>
<link href="https://fonts.googleapis.com/css2?family=Audiowide&family=Roboto:ital,wght@0,400;0,500;0,700;1,400&display=swap" rel="stylesheet">
<style>
:root{
  --dark:#15161c;
  --red:#d7101c;
  --wine:#8b1a24;
  --grey-bg:#efefef;
  --text:#5c5c5c;
  --ink:#111;
  --white:#fff;
}
*{box-sizing:border-box;margin:0;padding:0}
html,body{width:1200px;height:4559px;overflow:hidden}
body{font-family:"Roboto",sans-serif;color:var(--ink);background:var(--white);position:relative}
.abs{position:absolute}
.heading{font-family:"Audiowide",sans-serif;font-weight:400;text-transform:uppercase;letter-spacing:1px}
.btn{position:absolute;display:flex;align-items:center;justify-content:center;gap:8px;background:var(--red);color:var(--white);font-weight:700;border-radius:24px;text-transform:uppercase}
.arrow-dot{width:14px;height:14px;border-radius:50%;background:var(--white);display:inline-flex;align-items:center;justify-content:center}

/* header + hero */
.hero{position:absolute;left:0;top:0;width:1200px;height:735px;overflow:hidden}
.hero-photo{position:absolute;inset:0;background:radial-gradient(ellipse at 72% 62%,#8e141b 0%,#4a1014 22%,#2b2c30 48%,#141518 80%),linear-gradient(#3a3b3f,#101114)}
.topbar{position:absolute;left:0;top:0;width:1200px;height:118px;background:rgba(21,22,28,.96)}
.logo{left:111px;top:34px;color:var(--white)}
.logo-name{font-size:28px;font-weight:700;letter-spacing:2px}
.logo-sub{font-size:11px;letter-spacing:7px;text-align:center;margin-top:2px}
.call{left:690px;top:20px;display:flex;align-items:center;gap:10px;color:var(--white)}
.call-icon{width:34px;height:34px;border-radius:50%;background:var(--red);display:flex;align-items:center;justify-content:center}
.call small{display:block;font-size:10px;font-weight:500}
.call strong{display:block;font-size:17px;font-weight:700}
.appt-btn{left:906px;top:18px;width:181px;height:42px;border:2px solid var(--red);border-radius:22px;color:var(--white);font-size:14px;font-weight:700;display:flex;align-items:center;justify-content:center}
.nav{left:555px;top:84px;display:flex;gap:0;color:var(--white);font-size:15px;font-weight:500}
.nav a{color:inherit;text-decoration:none;position:relative;padding-bottom:10px}
.nav a.active{color:var(--red)}
.nav a.active::after{content:"";position:absolute;left:0;right:0;bottom:0;height:3px;background:var(--red)}
.hero-title{left:111px;top:212px;font-size:54px;color:var(--white)}
.hero-sub{left:111px;top:298px;width:400px;color:var(--white);font-size:17px;line-height:32px;font-weight:500}
.hero-btn{left:111px;top:393px;width:186px;height:47px;font-size:17px}
.dots{display:flex;gap:4px}
.dots span{width:11px;height:11px;border-radius:50%;border:2px solid var(--white)}
.dots span.on{background:var(--white)}

/* about */
.about-photo{left:108px;top:775px;width:407px;height:420px;border-radius:50%;background:radial-gradient(circle at 45% 55%,#c9c9c9 0%,#9a9a9a 35%,#c41a22 62%,#f0f0f0 74%)}
.about-title{left:600px;top:806px;font-size:40px}
.about-lead{left:602px;top:868px;font-size:20px;font-weight:500}
.body-copy{color:var(--text);font-size:14.5px;line-height:30px;text-align:justify}
.about-copy{left:600px;top:905px;width:488px}
.about-btn{left:600px;top:1112px;width:145px;height:40px;font-size:14px}

/* services */
.services{left:0;top:1300px;width:1200px;height:588px;background:var(--grey-bg)}
.section-title{width:1200px;text-align:center;font-size:40px;left:0}
.card{position:absolute;top:1435px;width:315px;height:375px;background:var(--white);border-bottom:3px solid var(--red);box-shadow:0 2px 6px rgba(0,0,0,.15)}
.card-photo{height:195px}
.card h3{font-size:19px;font-weight:500;margin:28px 8px 0}
.card p{font-size:14.5px;line-height:28px;color:var(--text);margin:10px 8px 0;text-align:justify}
.card .more{position:absolute;left:8px;bottom:22px;color:var(--red);font-weight:700;font-size:14.5px;display:flex;align-items:center;gap:6px}
.slide-arrow{position:absolute;top:1603px;width:40px;height:40px;border-radius:50%;background:var(--white);border:1px solid #ccc;display:flex;align-items:center;justify-content:center}

/* why */
.why-title{left:111px;top:1960px;font-size:40px}
.why-copy{left:111px;top:2022px;width:489px}
.feature{position:absolute;display:flex;align-items:center;gap:18px;font-size:16px}
.feature i{width:62px;height:62px;border-radius:50%;background:var(--dark);border:3px solid var(--red);display:flex;align-items:center;justify-content:center}
.why-frame{left:660px;top:1988px;width:423px;height:372px;border:3px solid var(--red)}
.why-photo{left:670px;top:1980px;width:418px;height:370px;background:linear-gradient(160deg,#8e969c,#4b5056 55%,#b0121c 70%,#777 90%)}

/* clients */
.clients{left:0;top:2448px;width:1200px;height:362px;background:var(--wine);color:var(--white)}
.quote{position:absolute;top:2590px;width:470px}
.avatar{position:absolute;left:0;top:0;width:84px;height:84px;border-radius:50%;background:#d9c2b2}
.quote p{position:absolute;left:124px;top:8px;width:340px;font-size:15px;font-style:italic;line-height:28px}
.quote .mark{position:absolute;font-family:Georgia,serif;font-size:34px;font-weight:700}
.quote b{position:absolute;left:124px;top:114px;font-size:15px;font-weight:500}

/* gallery */
.tile{position:absolute;width:238px}

/* appointment */
.booking{left:0;top:3497px;width:1200px;height:303px;background:var(--wine);color:var(--white)}
.field{position:absolute;background:var(--white);color:#777;font-size:14px;padding-left:18px;display:flex;align-items:center;border:1px solid #ccc}
.submit-white{position:absolute;background:var(--white);color:var(--ink);font-weight:700;font-size:14px;border-radius:20px;display:flex;align-items:center;justify-content:center}

/* partners */
.partner{position:absolute;top:3895px;width:186px;height:100px;background:var(--white);box-shadow:0 1px 6px rgba(0,0,0,.2);display:flex;align-items:center;justify-content:center;font-size:24px;font-weight:700;color:#1c2b6e}

/* footer */
.footer{left:0;top:4150px;width:1200px;height:409px;background:var(--dark);color:var(--white)}
.foot-h{position:absolute;top:4202px;font-size:17px;font-weight:500}
.foot-field{position:absolute;background:var(--white);color:#555;font-size:13px;padding-left:18px;display:flex;align-items:center}
.links{left:663px;top:4243px;font-size:14.5px;line-height:32px}
.contact-list{left:843px;top:4243px;font-size:14px;line-height:22px}
.contact-list div{display:flex;gap:12px;margin-bottom:10px}
.social{position:absolute;top:4470px;width:32px;height:32px;border-radius:50%;background:var(--white)}
.rule{left:111px;top:4510px;width:977px;height:1px;background:#888}
</style>
</head>
<body>

<!-- hero -->
<section class="hero">
  <div class="hero-photo" role="img" aria-label="Red sports car driving on a mountain road under a cloudy sky"></div>
  <svg class="abs" style="left:0;top:0" width="1200" height="735" viewBox="0 0 1200 735">
    <path d="M0 712 C300 660 560 600 760 630 C940 660 1080 680 1200 660 L1200 735 L0 735Z" fill="#8b1a24"/>
    <path d="M0 735 C320 690 560 620 780 650 C960 676 1090 690 1200 672 L1200 735Z" fill="#fff"/>
  </svg>
  <div class="topbar"></div>
  <div class="abs logo"><div class="logo-name">BRENVASHINE</div><div class="logo-sub">BODYSHOP</div></div>
  <div class="abs call">
    <span class="call-icon"><svg width="16" height="16" viewBox="0 0 24 24"><path d="M6.6 10.8a15 15 0 0 0 6.6 6.6l2.2-2.2c.3-.3.7-.4 1-.2 1.1.4 2.3.6 3.6.6.6 0 1 .4 1 1V20c0 .6-.4 1-1 1A17 17 0 0 1 3 4c0-.6.4-1 1-1h3.5c.6 0 1 .4 1 1 0 1.3.2 2.5.6 3.6.1.3 0 .7-.2 1z" fill="#fff"/></svg></span>
    <span><small>Call Us Today</small><strong>0770 914 2258</strong></span>
  </div>
  <div class="abs appt-btn">MAKE APPOINTMENT</div>
  <nav class="abs nav">
    <a class="active" href="#">Home</a>
    <a href="#" style="margin-left:39px">About Us</a>
    <a href="#" style="margin-left:40px">Service</a>
    <a href="#" style="margin-left:39px">Custom</a>
    <a href="#" style="margin-left:40px">Gallery</a>
    <a href="#" style="margin-left:40px">Contact</a>
  </nav>
  <h1 class="abs heading hero-title">BRENVASHINE</h1>
  <p class="abs hero-sub">Fully qualified trained technicians family run business established over 30 years</p>
  <div class="btn hero-btn">LEARN MORE <span class="arrow-dot"><svg width="8" height="8" viewBox="0 0 8 8"><path d="M2 1l3 3-3 3" stroke="#d7101c" stroke-width="1.6" fill="none"/></svg></span></div>
  <div class="abs dots" style="left:563px;top:552px"><span></span><span></span><span class="on"></span><span></span><span></span></div>
</section>

<!-- about -->
<div class="abs about-photo" role="img" aria-label="Vintage motorcycle in the workshop framed by a curled red and silver ribbon"></div>
<h2 class="abs heading about-title">ABOUT US</h2>
<p class="abs about-lead">Brenvashine Your One Stop Bodyshop</p>
<div class="abs about-copy body-copy">
  <p>Fully qualified trained technicians family run business established over 30 years. Brenvashine, based in Oakhollow, Wellshire established in August, 1985 has grown to become Wellshire's premiere manufacturer approved accident repair centre.</p>
  <p style="margin-top:8px">Equipped with the latest technology and factory trained technicians, we process accident repairs</p>
</div>
<div class="btn about-btn">READ MORE <span class="arrow-dot"><svg width="8" height="8" viewBox="0 0 8 8"><path d="M2 1l3 3-3 3" stroke="#d7101c" stroke-width="1.6" fill="none"/></svg></span></div>

<!-- services -->
<section class="abs services"></section>
<h2 class="abs heading section-title" style="top:1365px">OUR SERVICES</h2>
<div class="slide-arrow" style="left:33px"><svg width="10" height="10" viewBox="0 0 10 10"><path d="M6.5 1.5L3 5l3.5 3.5" stroke="#333" stroke-width="1.5" fill="none"/></svg></div>
<div class="slide-arrow" style="left:1125px"><svg width="10" height="10" viewBox="0 0 10 10"><path d="M3.5 1.5L7 5 3.5 8.5" stroke="#333" stroke-width="1.5" fill="none"/></svg></div>
<article class="card" style="left:111px">
  <div class="card-photo" role="img" aria-label="Car body in primer inside a spray booth" style="background:linear-gradient(#a07a78,#c98fa8 55%,#8d6a62)"></div>
  <h3>Full or part resprays</h3>
  <p>Sometimes a vehicle would simply benefit from having a complete new coat of paint.</p>
  <span class="more">READ MORE <svg width="14" height="14" viewBox="0 0 14 14"><circle cx="7" cy="7" r="5.6" stroke="#d7101c" stroke-width="1.5" fill="none"/><path d="M6 4.5L8.5 7 6 9.5" stroke="#d7101c" stroke-width="1.5" fill="none"/></svg></span>
</article>
<article class="card" style="left:442px">
  <div class="card-photo" role="img" aria-label="Technician repairing a dent on a dark car" style="background:linear-gradient(120deg,#1e1f24,#5b5e66 55%,#8a2420 80%,#9a9ea4)"></div>
  <h3>Dents &amp; scratch removal</h3>
  <p>The techniques used are methods that enable professionals to repair minor</p>
  <span class="more">READ MORE <svg width="14" height="14" viewBox="0 0 14 14"><circle cx="7" cy="7" r="5.6" stroke="#d7101c" stroke-width="1.5" fill="none"/><path d="M6 4.5L8.5 7 6 9.5" stroke="#d7101c" stroke-width="1.5" fill="none"/></svg></span>
</article>
<article class="card" style="left:773px">
  <div class="card-photo" role="img" aria-label="Silver car with a damaged front bumper" style="background:linear-gradient(#4b4d52,#9ea0a4 50%,#3d3f44)"></div>
  <h3>Bumper repair</h3>
  <p>Car bumper scuff damage can not only harm the appearance of your vehicle,</p>
  <span class="more">READ MORE <svg width="14" height="14" viewBox="0 0 14 14"><circle cx="7" cy="7" r="5.6" stroke="#d7101c" stroke-width="1.5" fill="none"/><path d="M6 4.5L8.5 7 6 9.5" stroke="#d7101c" stroke-width="1.5" fill="none"/></svg></span>
</article>

<!-- why us -->
<h2 class="abs heading why-title">WHY US</h2>
<p class="abs why-copy body-copy">As a small company we are able to offer an exceptionally personal service. Whenever you call us we aim for you to be able to speak directly to the person performing your car body repairs, who will give you plain speaking, objective advice. This, combined with our many years' experience and competitive prices makes us the perfect choice for those in need of any car body repair.</p>
<div class="feature" style="left:111px;top:2222px"><i><svg width="30" height="22" viewBox="0 0 30 22"><path d="M4 14l3-8h16l3 8v5H4z M7 14h16" stroke="#fff" stroke-width="2" fill="none"/></svg></i>Car body repairs</div>
<div class="feature" style="left:346px;top:2222px"><i><svg width="30" height="22" viewBox="0 0 30 22"><circle cx="7" cy="15" r="5" stroke="#fff" stroke-width="2" fill="none"/><circle cx="23" cy="15" r="5" stroke="#fff" stroke-width="2" fill="none"/><path d="M7 15l6-7h6l4 7" stroke="#fff" stroke-width="2" fill="none"/></svg></i>motorcycle painting</div>
<div class="feature" style="left:111px;top:2300px"><i><svg width="30" height="30" viewBox="0 0 30 30"><circle cx="15" cy="15" r="11" stroke="#fff" stroke-width="2" fill="none"/><circle cx="15" cy="15" r="4" stroke="#fff" stroke-width="2" fill="none"/></svg></i>wheel painting</div>
<div class="feature" style="left:346px;top:2300px"><i><svg width="32" height="22" viewBox="0 0 32 22"><path d="M3 15c0-4 4-6 8-6l4-4h6l5 5c3 0 4 2 4 5v2H3z" stroke="#fff" stroke-width="2" fill="none"/></svg></i>IE cars and bikes</div>
<div class="abs why-frame"></div>
<div class="abs why-photo" role="img" aria-label="Red classic car stripped for restoration in the workshop"></div>

<!-- clients -->
<section class="abs clients">
  <h2 class="abs heading section-title" style="top:48px">HAPPY CLIENTS</h2>
</section>
<div class="quote" style="left:111px;color:#fff">
  <div class="avatar" role="img" aria-label="Customer portrait"></div>
  <span class="mark" style="left:88px;top:-10px">&ldquo;</span>
  <p>We were extemely impressed with the service we received and the quality of the work carried out</p>
  <span class="mark" style="left:414px;top:42px">&rdquo;</span>
  <b>Mr T Halden</b>
</div>
<div class="quote" style="left:628px;color:#fff">
  <div class="avatar" role="img" aria-label="Customer portrait"></div>
  <span class="mark" style="left:88px;top:-10px">&ldquo;</span>
  <p>We were extemely impressed with the service we received and the quality of the work carried out</p>
  <span class="mark" style="left:414px;top:42px">&rdquo;</span>
  <b>Mr T Halden</b>
</div>
<div class="abs dots" style="left:111px;top:2776px"><span></span><span class="on"></span><span></span></div>

<!-- gallery -->
<h2 class="abs heading section-title" style="top:2895px">OUR GALLERY</h2>
<div class="tile" role="img" aria-label="Black car in the workshop" style="left:111px;top:2970px;height:238px;background:linear-gradient(#7a7c80,#1a1b1e)"></div>
<div class="tile" role="img" aria-label="Motorcycle on the showroom floor" style="left:111px;top:3217px;height:185px;background:linear-gradient(#5d6a5a,#1e1f22)"></div>
<div class="tile" role="img" aria-label="Car interior with white leather seats" style="left:358px;top:2970px;height:185px;background:linear-gradient(#2a2b2f,#c8c8c6)"></div>
<div class="tile" role="img" aria-label="Silver saloon car in the workshop" style="left:358px;top:3163px;height:239px;background:linear-gradient(#b7b0a2,#757a7e)"></div>
<div class="tile" role="img" aria-label="Rear of a silver sports car" style="left:604px;top:2970px;height:238px;background:linear-gradient(#9fa1a3,#5c5f62)"></div>
<div class="tile" role="img" aria-label="Car bodyshell in primer" style="left:604px;top:3217px;height:185px;background:linear-gradient(#d8d2c0,#8f9072)"></div>
<div class="tile" role="img" aria-label="Motorcycles lined up in a showroom" style="left:851px;top:2970px;height:185px;background:linear-gradient(#d8d8d8,#3a2d2d)"></div>
<div class="tile" role="img" aria-label="Red classic car under restoration" style="left:851px;top:3163px;height:239px;background:linear-gradient(#8a8f94,#b3141d 60%,#5a5c60)"></div>

<!-- appointment -->
<section class="abs booking">
  <h2 class="abs heading section-title" style="top:78px">MAKE AN APPOINMENT</h2>
  <p class="abs" style="left:0;top:124px;width:1200px;text-align:center;font-size:14.5px">Brenvashine Bodyshop, Harrow Trade Park, Ferne Lane, Oakhollow, Wellshire, WE12 7QT</p>
  <div class="field" style="left:117px;top:148px;width:313px;height:38px">Date</div>
  <div class="field" style="left:444px;top:148px;width:313px;height:38px">Date</div>
  <div class="field" style="left:770px;top:148px;width:312px;height:38px">Date</div>
  <div class="submit-white" style="left:545px;top:215px;width:110px;height:36px">SUBMIT</div>
</section>

<!-- partners -->
<div class="partner" style="left:111px;color:#333">KEBO</div>
<div class="partner" style="left:309px;color:#1c3aa8">GLENBRUSH</div>
<div class="partner" style="left:507px;color:#333">DORFLINT</div>
<div class="partner" style="left:705px;color:#1c3a8c">VASTINCO</div>
<div class="partner" style="left:903px;color:#c0141c">Q WRAP</div>

<!-- footer -->
<svg class="abs" style="left:0;top:4070px" width="1200" height="90" viewBox="0 0 1200 90"><path d="M0 80 C300 90 600 30 880 20 C1020 15 1130 25 1200 40 L1200 90 L0 90Z" fill="#15161c"/></svg>
<footer class="abs footer"></footer>
<div class="foot-h" style="left:111px;color:#fff">GET IN TOUCH</div>
<div class="foot-field" style="left:111px;top:4248px;width:236px;height:40px">First Name</div>
<div class="foot-field" style="left:354px;top:4248px;width:235px;height:40px">Last Name</div>
<div class="foot-field" style="left:111px;top:4297px;width:236px;height:40px">Email</div>
<div class="foot-field" style="left:354px;top:4297px;width:235px;height:40px">phone number</div>
<div class="foot-field" style="left:111px;top:4346px;width:478px;height:72px;align-items:flex-start;padding-top:14px">Message</div>
<div class="btn" style="left:111px;top:4442px;width:97px;height:34px;font-size:15px">SUBMIT</div>

<div class="foot-h" style="left:663px;color:#fff">QUICK LINKS</div>
<div class="abs links" style="color:#fff">
  <div>&rsaquo; Home</div><div>&rsaquo; About Us</div><div>&rsaquo; Service</div><div>&rsaquo; Custom</div><div>&rsaquo; Gallery</div><div>&rsaquo; Contact</div>
</div>

<div class="foot-h" style="left:843px;color:#fff">CONTACT US</div>
<div class="abs contact-list" style="color:#fff">
  <div><svg width="12" height="16" viewBox="0 0 12 16"><path d="M6 0a6 6 0 0 0-6 6c0 4.5 6 10 6 10s6-5.5 6-10a6 6 0 0 0-6-6zm0 8.5A2.5 2.5 0 1 1 6 3.5a2.5 2.5 0 0 1 0 5z" fill="#fff"/></svg><span>Harrow Trade Park, Ferne Lane,<br>Oakhollow, Wellshire, WE12 7QT</span></div>
  <div><svg width="14" height="14" viewBox="0 0 24 24"><path d="M6.6 10.8a15 15 0 0 0 6.6 6.6l2.2-2.2c.3-.3.7-.4 1-.2 1.1.4 2.3.6 3.6.6.6 0 1 .4 1 1V20c0 .6-.4 1-1 1A17 17 0 0 1 3 4c0-.6.4-1 1-1h3.5c.6 0 1 .4 1 1 0 1.3.2 2.5.6 3.6.1.3 0 .7-.2 1z" fill="#fff"/></svg><span>0770 914 2258</span></div>
  <div><svg width="14" height="12" viewBox="0 0 14 12"><rect x="1" y="1" width="12" height="10" stroke="#fff" fill="none" stroke-width="1.4"/><path d="M1 1l6 5 6-5" stroke="#fff" fill="none" stroke-width="1.4"/></svg><span>sales@brenvashine.co.uk</span></div>
  <div><svg width="14" height="14" viewBox="0 0 14 14"><circle cx="7" cy="7" r="6" stroke="#fff" fill="none" stroke-width="1.4"/><path d="M1 7h12M7 1c3 3 3 9 0 12M7 1c-3 3-3 9 0 12" stroke="#fff" fill="none" stroke-width="1.1"/></svg><span>brenvashine.co.uk</span></div>
</div>
<div class="social" style="left:845px"></div>
<div class="social" style="left:884px"></div>
<div class="social" style="left:923px"></div>

<div class="abs rule"></div>
<p class="abs" style="left:111px;top:4527px;font-size:13.5px;color:#fff">&copy; 2019 brenvashine. All Rights Reserved</p>
<p class="abs" style="left:984px;top:4522px;font-size:22px;font-weight:700;color:#fff">TILLWAVE</p>

</body>
</html>
```